Professional and creative business card design for recruiting service providers

Our company supports German medium-sized companies in filling vacancies promptly. For this we use social media marketing and bring our customers into the visibility.

We want a professional but also creative design for our business cards.

Please look at lindqvar-staff.de to get an impression of our CI.

Target Market(s)

Small and medium-sized companies in Germany from the industry

Industry/Entity Type

Industrie, Handwerk

Contact Information for Business Card

Name, Position, Telefonnummer, Email, Website

Colors
EE7325
F08F49
F5BC92
FAE3D3
FDF4ED

Requirements
Must have
• A picture of the employee and in the style of www.lindqvar-staff.de

```html
<!DOCTYPE html>
<html lang="de">
<head>
<meta charset="utf-8">
<title>Lindqvar Staff – Visitenkarte</title>
<link rel="stylesheet" href="https://fonts.googleapis.com/css2?family=Open+Sans:wght@400;700&family=Poppins:wght@700&display=swap">
<style>
  :root {
    --stage: #dcdde0;
    --card-dark: #060606;
    --pattern-tone: #141414;
    --card-light: #ffffff;
    --brand-orange: #ee5a2c;
    --ink: #111111;
    --muted: #5b5b5b;
    --rule: #cfcfcf;
    --photo-top: #d9d9d9;
    --photo-bottom: #4a4b4f;
  }
  * { box-sizing: border-box; margin: 0; padding: 0; }
  html, body { width: 1200px; height: 1000px; overflow: hidden; }
  body { background: var(--stage); font-family: "Open Sans", Arial, sans-serif; position: relative; }

  .card {
    position: absolute; left: 294px; width: 613px; height: 351px;
    border-radius: 24px; overflow: hidden;
    box-shadow: 0 22px 40px rgba(0,0,0,0.22);
  }
  .card--back { top: 82px; background: var(--card-dark); }
  .card--front { top: 523px; background: var(--card-light); }

  .back-texture {
    position: absolute; inset: 0;
    background: radial-gradient(circle at 40% 40%, var(--pattern-tone), var(--card-dark) 80%);
  }

  .wordmark { position: absolute; display: flex; align-items: center; gap: 12px; }
  .wordmark__square { background: var(--brand-orange); flex: none; }
  .wordmark__name {
    font-family: "Poppins", Arial, sans-serif; font-weight: 700; line-height: 1.05;
    letter-spacing: 0.5px; text-transform: uppercase;
  }
  .card--back .wordmark { left: 349px; top: 213px; }
  .card--back .wordmark__square { width: 50px; height: 50px; }
  .card--back .wordmark__name { color: #ffffff; font-size: 21px; }

  .portrait {
    position: absolute; left: 0; top: 0; width: 303px; height: 100%;
    background: linear-gradient(180deg, var(--photo-top) 0%, #b9b6b2 45%, var(--photo-bottom) 100%);
  }

  .contact { position: absolute; left: 336px; top: 42px; right: 20px; }
  .contact__name { color: var(--brand-orange); font-weight: 700; font-size: 23px; line-height: 1.2; }
  .contact__role { color: var(--ink); font-size: 13.5px; margin-top: 2px; }
  .contact__list { list-style: none; margin-top: 26px; }
  .contact__item { display: flex; align-items: center; gap: 9px; height: 30px; margin-bottom: 13px; color: var(--muted); font-size: 16px; }
  .contact__icon {
    width: 30px; height: 30px; border-radius: 50%; background: var(--brand-orange);
    display: flex; align-items: center; justify-content: center; flex: none;
  }

  .front-rule { position: absolute; left: 303px; right: 0; top: 269px; border-top: 1px solid var(--rule); }
  .card--front .wordmark { left: 390px; top: 291px; gap: 9px; }
  .card--front .wordmark__square { width: 34px; height: 34px; }
  .card--front .wordmark__name { color: var(--ink); font-size: 13.5px; }
</style>
</head>
<body>

<section class="card card--back">
  <div class="back-texture" role="img" aria-label="Dunkles Kachelmuster aus dem Firmenzeichen"></div>
  <div class="wordmark">
    <span class="wordmark__square"></span>
    <span class="wordmark__name">Lindqvar<br>Staff</span>
  </div>
</section>

<section class="card card--front">
  <div class="portrait" role="img" aria-label="Porträtfoto des Mitarbeiters im Anzug im Büro"></div>
  <div class="contact">
    <h1 class="contact__name">Jonas Brevik</h1>
    <p class="contact__role">Senior Recruiting Berater</p>
    <ul class="contact__list">
      <li class="contact__item">
        <span class="contact__icon">
          <svg width="16" height="16" viewBox="0 0 24 24" fill="#fff"><path d="M6.6 10.8a15.1 15.1 0 0 0 6.6 6.6l2.2-2.2c.3-.3.7-.4 1-.2 1.1.4 2.3.6 3.6.6.6 0 1 .4 1 1V20c0 .6-.4 1-1 1C10.6 21 3 13.4 3 4c0-.6.4-1 1-1h3.5c.6 0 1 .4 1 1 0 1.3.2 2.5.6 3.6.1.3 0 .7-.2 1z"/></svg>
        </span>
        0176 304 2719
      </li>
      <li class="contact__item">
        <span class="contact__icon">
          <svg width="16" height="16" viewBox="0 0 24 24" fill="none" stroke="#fff" stroke-width="2"><rect x="3" y="6" width="18" height="12" rx="1"/><path d="M3 7l9 6 9-6"/></svg>
        </span>
        info@lindqvar-staff.de
      </li>
      <li class="contact__item">
        <span class="contact__icon">
          <svg width="16" height="16" viewBox="0 0 24 24" fill="none" stroke="#fff" stroke-width="1.8"><circle cx="12" cy="12" r="9"/><ellipse cx="12" cy="12" rx="4" ry="9"/><path d="M3 12h18M5 7.5h14M5 16.5h14"/></svg>
        </span>
        lindqvar-staff.de
      </li>
    </ul>
  </div>
  <div class="front-rule"></div>
  <div class="wordmark">
    <span class="wordmark__square"></span>
    <span class="wordmark__name">Lindqvar<br>Staff</span>
  </div>
</section>

</body>
</html>
```